Flyer for spiritual retreat (yoga, meditation, reiki, raw food)

I would like a flyer to promote my upcoming retreat and a matching Facebook banner.

The name of the retreat is "OutBloom the Spirit" and the tagline is "retreat into you"

The activities in the retreat include daily meditation, ecstatic dance, spiritual development workshops on intuition, energy healing etc and a reiki session is included.

I would like a flyer designed to promote this, something that is editable as I will be running this multiple times and will need to adjust the flyer to add the dates etc each time.

edit: add that here will be fully catered raw food and juices, and that the retreat price includes all accomodation, meals and workshops.

Please contact me if you need further info. Please also visit my website www.marlavosk.com and www.pagenest.com/koruhaven to see my current events and promotions.

Thank you,

Marla

Reason: Hi all, thank you all for your submissions. Apologies as I am traveling and do not have much access to internet and will review your submissions and provide feedback as soon as possible. Kind regards, Marla.

Target Market(s)

People who like meditation, yoga, fans of tomas brenner and wendell marsh, those interested in personal and spiritual development.

Industry/Entity Type

Health And Wellness

Requirements
Must have
• Please put the included reiki session as as added bonus. Something like "BONUS 30 minute reiki healing session" in a little star/banner/something that stands out.
• Please emphasise the "light" part of OutBloom as I am going for a play on words between in the light and enlightenment.
• Please include placeholder text for place, location, time
• Placeholder for price
• My name (see attached file - can change colour to suit) and website (www.marlavosk.com)
Nice to have
• I prefer rounded designs, curves rather than block designs.
Should not have
• Koru Haven logo

```html
<!DOCTYPE html>
<html lang="en">
<head>
<meta charset="utf-8">
<title>OutBloom the Spirit – retreat into you</title>
<link rel="stylesheet" href="https://fonts.googleapis.com/css2?family=Libre+Baskerville:wght@400;700&family=Great+Vibes&family=Raleway:wght@300&family=Roboto+Condensed:wght@400&family=Pinyon+Script&family=Roboto:wght@400&display=swap">
<style>
  :root {
    --ink: #221f20;
    --gold: #f0d75a;
    --gold-deep: #b8913a;
    --gold-light: #fff1b8;
    --cream: #f6ecbd;
    --white: #ffffff;
    --label: #e8e4dc;
  }
  * { margin: 0; padding: 0; box-sizing: border-box; }
  html, body { width: 848px; height: 1200px; overflow: hidden; background: var(--ink); }
  .flyer {
    position: relative;
    width: 848px;
    height: 1200px;
    overflow: hidden;
    background: var(--ink);
    color: var(--white);
  }
  .hero-art {
    position: absolute;
    inset: 0 0 auto 0;
    height: 700px;
    background:
      radial-gradient(ellipse 130px 240px at 412px 300px, rgba(255,240,170,0.85), rgba(230,190,80,0.35) 55%, transparent 80%),
      radial-gradient(ellipse 420px 260px at 220px 360px, rgba(190,150,60,0.55), transparent 70%),
      radial-gradient(ellipse 300px 180px at 640px 480px, rgba(160,130,50,0.45), transparent 75%),
      radial-gradient(ellipse 500px 200px at 500px 120px, rgba(120,95,45,0.5), transparent 75%),
      linear-gradient(180deg, #2a2620 0%, #4a3f26 35%, #3b3424 65%, var(--ink) 100%);
  }
  .title {
    position: absolute;
    left: 40px;
    right: 40px;
    top: 560px;
    display: flex;
    justify-content: center;
    align-items: baseline;
    white-space: nowrap;
    font-family: "Libre Baskerville", Georgia, serif;
    font-weight: 700;
    font-size: 50px;
    color: var(--white);
    text-shadow: 0 0 8px rgba(0,0,0,0.5);
  }
  .title-accent {
    font-family: "Great Vibes", cursive;
    font-weight: 400;
    font-size: 118px;
    line-height: 1;
    margin: 0 10px 0 4px;
    background: linear-gradient(180deg, var(--gold-light) 10%, var(--gold) 45%, var(--gold-deep) 90%);
    -webkit-background-clip: text;
    background-clip: text;
    color: transparent;
    text-shadow: none;
    filter: drop-shadow(0 2px 3px rgba(0,0,0,0.6));
  }
  .tagline {
    position: absolute;
    left: 262px;
    top: 662px;
    font-family: "Raleway", sans-serif;
    font-weight: 300;
    font-size: 32px;
    letter-spacing: 17px;
    color: var(--white);
  }
  .event-date {
    position: absolute;
    right: 68px;
    top: 706px;
    font-family: "Roboto Condensed", "Arial Narrow", sans-serif;
    font-size: 42px;
    color: var(--gold);
  }
  .event-date sup { font-size: 22px; vertical-align: 18px; }
  .activities {
    position: absolute;
    left: 282px;
    top: 772px;
    width: 520px;
    font-family: "Roboto Condensed", "Arial Narrow", sans-serif;
    font-size: 24px;
    line-height: 34px;
    color: var(--cream);
  }
  .bonus-badge {
    position: absolute;
    left: 74px;
    top: 760px;
    width: 176px;
    height: 176px;
    border: 2px solid var(--gold);
    border-radius: 50%;
    display: flex;
    flex-direction: column;
    align-items: center;
    justify-content: center;
    text-align: center;
    font-family: "Roboto Condensed", "Arial Narrow", sans-serif;
    color: var(--white);
    font-size: 23px;
    line-height: 29px;
    box-shadow: -6px -4px 14px -6px rgba(255,240,170,0.5);
  }
  .bonus-badge .bonus-word { color: var(--gold); font-size: 30px; line-height: 36px; }
  .details {
    position: absolute;
    left: 286px;
    top: 895px;
    width: 496px;
    list-style: none;
  }
  .details li {
    display: flex;
    align-items: center;
    height: 26px;
    margin-bottom: 16px;
    font-family: "Roboto", Arial, sans-serif;
    font-size: 18px;
    color: var(--label);
  }
  .details .field-label { width: 86px; }
  .details .field-blank {
    flex: 1;
    height: 26px;
    background: var(--white);
    border-radius: 13px;
  }
  .host-name {
    position: absolute;
    right: 116px;
    top: 1082px;
    font-family: "Pinyon Script", cursive;
    font-size: 36px;
    color: var(--white);
    text-shadow: 0 0 6px rgba(255,255,255,0.4);
  }
  .website {
    position: absolute;
    right: 38px;
    top: 1142px;
    font-family: "Roboto", Arial, sans-serif;
    font-size: 17px;
    color: var(--white);
  }
</style>
</head>
<body>
  <main class="flyer">
    <div class="hero-art" role="img" aria-label="Golden star tetrahedron framing a glowing human figure against a starry golden nebula"></div>

    <h1 class="title">Out<span class="title-accent">Bloom</span>the Spirit</h1>
    <p class="tagline">retreat into you</p>
    <p class="event-date">15<sup>th</sup> January 2017</p>

    <div class="bonus-badge">
      <span class="bonus-word">BONUS</span>
      <span>30 minute</span>
      <span>Reiki Healing</span>
      <span>Session</span>
    </div>

    <p class="activities">The activities in the retreat include daily meditation, ecstatic dance, spiritual development workshops on intuition, energy healing etc</p>

    <ul class="details">
      <li><span class="field-label">Place</span><span class="field-blank"></span></li>
      <li><span class="field-label">Location</span><span class="field-blank"></span></li>
      <li><span class="field-label">Time</span><span class="field-blank"></span></li>
      <li><span class="field-label">Price</span><span class="field-blank"></span></li>
    </ul>

    <p class="host-name">Marla Vosk</p>
    <p class="website">www.marlavosk.com</p>
  </main>
</body>
</html>
```